Advertising company unique advertising platform

we need a logo design for a new company based in Australia Melbourne. We develop innovated advertising platform where consumer can use this platform to get regular discount, as business owner they can use this platform for free advertisement. Payment for this advertisement platform only payable every two weeks, when I generate revenue for their business

Industry/Entity Type

Advertising

Contact Information for Business Card

Dale Morven | Co-Founder |Managing Director
Suite 718 240 Wattlebrook Lane Melbourne Vic 3000

ABN 38 614 207 923
Tel: +61 0487 259 318 | Email: dale.morven@plivorantu.com

Font styles to use
Decorative
Script

Requirements
Must have
• Try few different design and some round corner business card
Should not have
• One round corner business card...try 4 different colour background not only black, make sure two side is designed. Be creative so imagine you are giving this to a client make sure has wow factor, if you can also try one design with engrave like all the logo, words look 3d feel
• The word Advertising Platform use attached file font

```html
<!DOCTYPE html>
<html lang="en">
<head>
<meta charset="utf-8">
<title>Wattle Loop — Business Card</title>
<link href="https://fonts.googleapis.com/css2?family=Roboto:wght@400;500;700&display=swap" rel="stylesheet">
<style>
  :root {
    --page-bg: #e9e6e2;
    --front-edge: #e2452a;
    --front-mid: #f07a2a;
    --front-core: #f6c542;
    --ink-dark: #1c1b1a;
    --card-dark: #262626;
    --card-dark-edge: #1e1e1e;
    --text-light: #f2f2f2;
    --accent-red: #f0492f;
    --accent-green: #27e0a0;
    --rule: #d8d8d8;
    --bar-top: #f6a02a;
    --bar-bottom: #e8392b;
  }
  * { margin: 0; padding: 0; box-sizing: border-box; }
  html, body { width: 1200px; height: 886px; overflow: hidden; }
  body {
    background: var(--page-bg);
    font-family: "Roboto", Arial, sans-serif;
    position: relative;
  }
  .card {
    position: absolute;
    width: 540px;
    height: 330px;
    border-radius: 22px;
    overflow: hidden;
    box-shadow: 0 14px 30px rgba(0,0,0,0.22);
  }
  /* Front side */
  .card-front { left: 40px; top: 150px; }
  .front-backdrop {
    position: absolute; inset: 0;
    background: radial-gradient(ellipse 60% 60% at 50% 48%, var(--front-core) 0%, var(--front-mid) 55%, var(--front-edge) 100%);
  }
  .front-brand {
    position: absolute; left: 0; right: 0; top: 118px;
    text-align: center;
  }
  .brand-name {
    font-weight: 700;
    font-size: 54px;
    letter-spacing: 1px;
    color: var(--ink-dark);
    line-height: 1;
  }
  .brand-web {
    margin-top: 14px;
    font-size: 12px;
    font-weight: 500;
    letter-spacing: 4px;
    color: var(--ink-dark);
  }
  /* Back side */
  .card-back {
    left: 620px; top: 400px;
    background: linear-gradient(160deg, var(--card-dark) 0%, var(--card-dark-edge) 100%);
    color: var(--text-light);
  }
  .back-logo {
    position: absolute; left: 34px; top: 40px;
    display: flex; align-items: center; gap: 12px;
  }
  .logo-dot {
    width: 46px; height: 46px; border-radius: 50%;
    background: var(--front-mid);
  }
  .logo-name {
    font-weight: 700; font-size: 34px; color: var(--accent-red);
  }
  .rule {
    position: absolute; height: 1px; background: var(--rule);
  }
  .rule-top { left: 30px; right: 30px; top: 112px; }
  .rule-bottom { left: 160px; right: 30px; top: 200px; }
  .person {
    position: absolute; right: 40px; top: 128px; text-align: right;
    line-height: 1.1;
  }
  .person-name { font-size: 20px; font-weight: 500; color: var(--accent-red); }
  .person-role { font-size: 15px; font-weight: 500; color: var(--accent-green); }
  .side-bar {
    position: absolute; right: 0; top: 138px;
    width: 10px; height: 56px;
    background: linear-gradient(180deg, var(--bar-top), var(--bar-bottom));
  }
  .contact {
    position: absolute; left: 30px; right: 30px; top: 222px;
    text-align: center; font-size: 14px; line-height: 1.6;
  }
  .label { color: var(--accent-red); font-weight: 500; }
</style>
</head>
<body>
  <section class="card card-front">
    <div class="front-backdrop" role="img" aria-label="Orange to golden radial backdrop with a faint repeating flame pattern"></div>
    <div class="front-brand">
      <div class="brand-name">Wattle Loop</div>
      <div class="brand-web">www.plivorantu.com</div>
    </div>
  </section>

  <section class="card card-back">
    <div class="back-logo">
      <span class="logo-dot"></span>
      <span class="logo-name">Wattle Loop</span>
    </div>
    <div class="rule rule-top"></div>
    <div class="person">
      <div class="person-name">DALE MORVEN</div>
      <div class="person-role">CO-FOUNDER</div>
      <div class="person-role">MANAGING DIRECTOR</div>
    </div>
    <div class="side-bar"></div>
    <div class="rule rule-bottom"></div>
    <div class="contact">
      <div>Suite 718 240 Wattlebrook Lane, Melbourne Vic 3000</div>
      <div><span class="label">Phone:</span> +61 0487 259 318 | <span class="label">Email:</span> dale.morven@plivorantu.com</div>
      <div>Plivorantu | ABN 38 614 207 923</div>
    </div>
  </section>
</body>
</html>
```